Global (re)insurance broker needs a business card design

We need a classic business card for our company that is headquartered in SG, with offices in Malaysia and Dubai. We specialise in insurance and reinsurance broking and consultancy for our global clients.

```html
<!DOCTYPE html>
<html lang="en">
<head>
<meta charset="utf-8">
<title>Business Card – Meridan</title>
<link href="https://fonts.googleapis.com/css2?family=Montserrat:wght@400;500;700&display=swap" rel="stylesheet">
<style>
  :root {
    --brand-blue: #26479a;
    --brand-green: #c2dbb6;
    --paper: #ffffff;
    --backdrop: #3a3a3a;
    --ink-light: #ffffff;
  }
  * { box-sizing: border-box; margin: 0; padding: 0; }
  html, body {
    width: 1200px; height: 1200px; overflow: hidden;
    background: var(--backdrop);
    font-family: "Montserrat", sans-serif;
  }
  .stage {
    width: 1200px; height: 1200px;
    display: flex; flex-direction: column; align-items: center; justify-content: center;
    gap: 60px;
  }
  .card {
    width: 900px; height: 514px;
    border-radius: 34px;
    overflow: hidden;
    position: relative;
    box-shadow: 0 10px 24px rgba(0,0,0,0.35);
  }
  /* Front */
  .card-front { background: var(--paper); display: flex; }
  .contact-panel {
    width: 418px; height: 100%;
    background: var(--brand-blue);
    color: var(--ink-light);
    padding: 150px 0 0 84px;
  }
  .divider {
    width: 12px; height: 100%;
    margin-left: 12px;
    background: var(--brand-green);
  }
  .logo-area {
    flex: 1; display: flex; align-items: center; justify-content: center;
    padding-left: 20px;
  }
  .holder-name { font-size: 34px; font-weight: 700; letter-spacing: 0.5px; line-height: 1; }
  .holder-position { font-size: 21px; font-weight: 400; letter-spacing: 1px; margin-top: 4px; }
  .contact-list { list-style: none; margin-top: 22px; margin-left: 34px; }
  .contact-list li {
    display: flex; align-items: flex-start; gap: 12px;
    font-size: 18px; line-height: 1.25; margin-bottom: 6px;
  }
  .contact-list svg { width: 20px; height: 20px; flex: none; margin-top: 2px; fill: var(--ink-light); }
  .wordmark {
    font-weight: 700; letter-spacing: 2px;
    color: var(--brand-blue);
    font-size: 64px;
  }
  /* Back */
  .card-back {
    background: var(--brand-blue);
    display: flex; align-items: center; justify-content: center;
  }
  .card-back .wordmark { color: var(--ink-light); font-size: 116px; letter-spacing: 4px; }
</style>
</head>
<body>
<main class="stage">
  <section class="card card-front">
    <div class="contact-panel">
      <h1 class="holder-name">FULL NAME</h1>
      <p class="holder-position">POSITION</p>
      <ul class="contact-list">
        <li>
          <svg viewBox="0 0 24 24" aria-hidden="true"><path d="M6.6 10.8a15.1 15.1 0 0 0 6.6 6.6l2.2-2.2c.3-.3.7-.4 1-.2 1.1.4 2.3.6 3.6.6.6 0 1 .4 1 1V20c0 .6-.4 1-1 1A17 17 0 0 1 3 4c0-.6.4-1 1-1h3.5c.6 0 1 .4 1 1 0 1.3.2 2.5.6 3.6.1.3 0 .7-.2 1z"/></svg>
          <span>(000) 000 0000</span>
        </li>
        <li>
          <svg viewBox="0 0 24 24" aria-hidden="true"><path d="M2 5h20v14H2zm2 2v.5l8 5 8-5V7zm0 2.8V17h16V9.8l-8 5z"/></svg>
          <span>email@company.com</span>
        </li>
        <li>
          <svg viewBox="0 0 24 24" aria-hidden="true"><path d="M12 2a10 10 0 1 0 0 20 10 10 0 0 0 0-20zm6.9 6h-3a15 15 0 0 0-1.3-4A8 8 0 0 1 18.9 8zM12 4c.8 1.1 1.5 2.5 1.9 4h-3.8c.4-1.5 1.1-2.9 1.9-4zM4.3 14a8 8 0 0 1 0-4h3.4a16 16 0 0 0 0 4zm.8 2h3a15 15 0 0 0 1.3 4A8 8 0 0 1 5.1 16zm3-8h-3a8 8 0 0 1 4.3-4c-.6 1.2-1 2.6-1.3 4zM12 20c-.8-1.1-1.5-2.5-1.9-4h3.8c-.4 1.5-1.1 2.9-1.9 4zm2.3-6H9.7a14 14 0 0 1 0-4h4.6a14 14 0 0 1 0 4zm.3 6c.6-1.2 1-2.6 1.3-4h3a8 8 0 0 1-4.3 4zm1.7-6a16 16 0 0 0 0-4h3.4a8 8 0 0 1 0 4z"/></svg>
          <span>www.company.com</span>
        </li>
        <li>
          <svg viewBox="0 0 24 24" aria-hidden="true"><path d="M12 2a7 7 0 0 0-7 7c0 5 7 13 7 13s7-8 7-13a7 7 0 0 0-7-7zm0 9.5A2.5 2.5 0 1 1 12 6.5a2.5 2.5 0 0 1 0 5z"/></svg>
          <span>123 Name Street, 000<br>Your City, 00000-000</span>
        </li>
      </ul>
    </div>
    <div class="divider"></div>
    <div class="logo-area">
      <span class="wordmark">MERIDAN</span>
    </div>
  </section>

  <section class="card card-back">
    <span class="wordmark">MERIDAN</span>
  </section>
</main>
</body>
</html>
```